Lumbra Ember Oven Kitchen (restaurant)

Restaurant with a cool vibe.
We need a refresh of existing site. Appealing to a hip crowd of 25 or older age bracket (mid price to high small town). Constant changes food and cocktail menu. A vibing atmosphere with jazz funk hip music.
Must be able to scale for any device… phone/mobile device super important.
Instagram: @Lumbra.Bexwell
Website: lumbrabexwell.example

Target Market(s)

25-55 age group

Number of Pages Required

1 page

Font styles to use
Sans Serif

Requirements
Must have
• Simple to navigate. Simplicity is the key to all sophistication.

Links/Buttons
Menu
Gift Cards
Reservations
Take Out
Contact Us
Should not have
• Please, nothing generic looking… no cookie cutter look. Originality

```html
<!DOCTYPE html>
<html lang="en">
<head>
<meta charset="utf-8">
<title>Lumbra Ember Oven Kitchen</title>
<link href="https://fonts.googleapis.com/css2?family=Alfa+Slab+One&family=Poppins:wght@400;500;600;700&display=swap" rel="stylesheet">
<style>
:root{
  --red:#f20d0d;
  --black:#0b0b0b;
  --white:#ffffff;
  --grey-bg:#f2f2f2;
  --text:#222222;
  --muted:#666666;
  --line:#cfcfcf;
  --heading:'Alfa Slab One', Georgia, serif;
  --body:'Poppins', Arial, sans-serif;
}
*{box-sizing:border-box;margin:0;padding:0}
html,body{width:1200px;height:3552px;overflow:hidden;background:var(--white)}
body{position:relative;font-family:var(--body);color:var(--text)}
.section{position:absolute;left:0;width:1200px}
.wave{position:absolute;left:0;width:1200px;height:40px;display:block}

/* hero */
.hero{top:0;height:620px;overflow:hidden}
.hero-bg{position:absolute;inset:0;background:linear-gradient(160deg,#5a1a1e 0%,#8e2a2c 35%,#3d2a2e 65%,#1d1c24 100%)}
.hero-bg::after{content:"";position:absolute;inset:0;background:rgba(0,0,0,.38)}
.nav{position:absolute;top:0;left:0;width:1200px;height:96px;display:flex;align-items:center;justify-content:space-between;padding:0 120px 0 140px;z-index:2}
.brand{font-family:var(--heading);color:var(--white);font-size:22px;letter-spacing:1px}
.nav-links{display:flex;gap:34px;list-style:none}
.nav-links a{color:var(--white);text-decoration:none;font-size:15px;font-weight:600;letter-spacing:.5px}
.hero-title{position:absolute;top:204px;width:100%;text-align:center;font-family:var(--heading);color:var(--white);font-size:66px;line-height:76px;letter-spacing:2px;z-index:2}
.hero-title .accent{color:var(--red)}
.hero-actions{position:absolute;top:404px;width:100%;display:flex;justify-content:center;gap:28px;z-index:2}
.btn{display:inline-flex;align-items:center;justify-content:center;height:56px;padding:0 38px;border-radius:28px;font-size:15px;font-weight:600;text-decoration:none;letter-spacing:.5px;font-family:var(--body)}
.btn-outline{border:2px solid var(--white);color:var(--white)}
.btn-black{background:var(--black);color:var(--white)}
.btn-red{background:var(--red);color:var(--white)}
.hero-dots{position:absolute;right:36px;top:330px;display:flex;flex-direction:column;gap:14px;z-index:2}
.hero-dots span{width:8px;height:8px;border-radius:50%;background:var(--white);opacity:.6}
.hero-dots span:first-child{opacity:1}

.section-title{position:absolute;width:100%;text-align:center;font-family:var(--heading);font-size:48px;letter-spacing:1px;color:var(--black)}
.section-title .accent{color:var(--red)}

/* gift cards */
.gift{top:620px;height:440px}
.gift .section-title{top:52px}
.gift-cards{position:absolute;top:160px;left:148px;display:flex;gap:18px}
.gift-card{width:288px;height:200px;border:5px solid var(--red);position:relative;display:flex;align-items:center;justify-content:center;box-shadow:0 6px 14px rgba(0,0,0,.25)}
.gift-card .photo{position:absolute;inset:0}
.gift-card span{position:relative;color:var(--white);font-weight:600;font-size:20px;letter-spacing:.5px;margin-top:70px}

/* menu */
.menu{top:1060px;height:640px;background:var(--grey-bg)}
.menu .section-title{top:86px}
.menu-items{position:absolute;top:200px;left:166px;display:flex;gap:60px}
.menu-item{width:172px;text-align:center}
.menu-item .photo{width:172px;height:172px;border-radius:50%}
.menu-item h3{margin-top:26px;font-size:19px;font-weight:700;letter-spacing:.5px;color:var(--black)}
.arrow{position:absolute;width:44px;height:44px;border-radius:50%;border:2px solid #999;display:flex;align-items:center;justify-content:center;background:var(--white)}
.actions{position:absolute;width:100%;display:flex;justify-content:center;gap:16px}
.menu .actions{top:496px}

/* take out */
.takeout{top:1700px;height:648px}
.takeout .section-title{top:104px}
.takeout-photos{position:absolute;top:200px;left:144px;display:flex;gap:16px}
.takeout-photos .photo{width:216px;height:212px}
.takeout .actions{top:480px}

/* reservations */
.reserve{top:2348px;height:632px}
.reserve-photo{position:absolute;left:600px;top:0;width:600px;height:632px;background:linear-gradient(135deg,#a54a2a 0%,#c8543a 30%,#7a3e2c 55%,#3f6a3a 80%,#d24a6a 100%)}
.reserve-card{position:absolute;left:140px;top:44px;width:600px;height:548px;background:var(--white);box-shadow:0 10px 30px rgba(0,0,0,.28);padding:70px 56px 0}
.reserve-card h2{font-family:var(--heading);font-size:46px;text-align:center;letter-spacing:1px;color:var(--black);line-height:1}
.form{margin-top:60px;display:grid;grid-template-columns:1fr 1fr;gap:18px 20px}
.field{height:40px;border:1px solid var(--line);font-size:12px;color:var(--muted);padding:0 12px;display:flex;align-items:center;justify-content:space-between}
.field.full{grid-column:1 / 3;height:92px;align-items:flex-start;padding-top:12px}
.submit{display:flex;justify-content:center;margin-top:30px}
.submit .btn{width:190px;height:62px;border-radius:31px}

/* contact */
.contact{top:2980px;height:508px}
.contact .section-title{top:80px}
.contact-cols{position:absolute;top:196px;left:152px;display:grid;grid-template-columns:300px 388px 300px}
.contact-cols h3{font-size:20px;font-weight:700;color:var(--black);margin-bottom:14px}
.contact-cols h3.spaced{margin-top:22px}
.contact-cols p{font-size:13px;color:var(--text);line-height:30px}
.info{list-style:none}
.info li{display:flex;align-items:center;gap:14px;font-size:13px;line-height:30px}
.info svg{flex:none}

/* footer */
.footer{top:3488px;height:64px;background:var(--black);color:var(--white);text-align:center;font-size:11px;padding-top:30px}
</style>
</head>
<body>

<svg width="0" height="0" style="position:absolute">
  <defs>
    <pattern id="scallop-white" width="40" height="40" patternUnits="userSpaceOnUse">
      <path d="M0 40 L0 22 Q10 10 20 22 Q30 34 40 22 L40 40 Z" fill="#ffffff"/>
    </pattern>
    <pattern id="scallop-black" width="40" height="40" patternUnits="userSpaceOnUse">
      <path d="M0 40 L0 22 Q10 10 20 22 Q30 34 40 22 L40 40 Z" fill="#0b0b0b"/>
    </pattern>
  </defs>
</svg>

<header class="section hero">
  <div class="hero-bg" role="img" aria-label="Wood-fired pizza and drinks on a restaurant table"></div>
  <nav class="nav">
    <div class="brand">Lumbra Ember Oven Kitchen</div>
    <ul class="nav-links">
      <li><a href="#gift">GIFT CARDS</a></li>
      <li><a href="#menu">MENU</a></li>
      <li><a href="#contact">CONTACT US</a></li>
      <li><a href="#reserve">RESERVATIONS</a></li>
      <li><a href="#takeout">TAKE OUT</a></li>
    </ul>
  </nav>
  <h1 class="hero-title">LETS GET LUNCH<br>AT <span class="accent">LUMBRA!</span></h1>
  <div class="hero-actions">
    <a class="btn btn-outline" href="#takeout">ORDER ONLINE</a>
    <a class="btn btn-black" href="#reserve">BOOK A TABLE</a>
    <a class="btn btn-outline" href="#contact">HOURS &amp; CONTACT</a>
  </div>
  <div class="hero-dots"><span></span><span></span><span></span></div>
  <svg class="wave" style="bottom:0" viewBox="0 0 1200 40"><rect width="1200" height="40" fill="url(#scallop-white)"/></svg>
</header>

<section class="section gift" id="gift">
  <h2 class="section-title">GIFT <span class="accent">CARDS</span></h2>
  <div class="gift-cards">
    <div class="gift-card"><div class="photo" role="img" aria-label="Gift card with a plated dish" style="background:linear-gradient(135deg,#3a3a3a,#6b5a52 50%,#2a2a2a)"></div><span>LOREM IPSOLOR</span></div>
    <div class="gift-card"><div class="photo" role="img" aria-label="Gift card with a wood-fired pizza" style="background:linear-gradient(135deg,#4a2a22,#8a5a3a 50%,#2e2420)"></div><span>EXCEPTEUR</span></div>
    <div class="gift-card"><div class="photo" role="img" aria-label="Gift card with a pasta dish" style="background:linear-gradient(135deg,#3e3a30,#7a6a4a 50%,#2a2620)"></div><span>NEMO ENIM IPSAM</span></div>
  </div>
</section>

<section class="section menu" id="menu">
  <h2 class="section-title">OUR <span class="accent">MENU</span></h2>
  <div class="arrow" style="left:70px;top:266px"><svg width="14" height="14" viewBox="0 0 14 14"><path d="M9 2 L4 7 L9 12" fill="none" stroke="#555" stroke-width="2"/></svg></div>
  <div class="menu-items">
    <div class="menu-item"><div class="photo" role="img" aria-label="Fresh salad" style="background:radial-gradient(circle,#d94a3a,#7a3a2a 70%,#4a2a20)"></div><h3>SALADS</h3></div>
    <div class="menu-item"><div class="photo" role="img" aria-label="Toasted sandwich" style="background:radial-gradient(circle,#c89a6a,#6a4a34 70%,#3a2a20)"></div><h3>SANDWICHES</h3></div>
    <div class="menu-item"><div class="photo" role="img" aria-label="Burger with greens" style="background:radial-gradient(circle,#9a8a4a,#4a5a2a 70%,#2a2a1a)"></div><h3>BURGERS</h3></div>
    <div class="menu-item"><div class="photo" role="img" aria-label="Pizza and pasta" style="background:radial-gradient(circle,#c85a3a,#7a3a2a 70%,#3a2418)"></div><h3>MAINS &amp; PASTA</h3></div>
  </div>
  <div class="arrow" style="left:1084px;top:266px"><svg width="14" height="14" viewBox="0 0 14 14"><path d="M5 2 L10 7 L5 12" fill="none" stroke="#555" stroke-width="2"/></svg></div>
  <div class="actions">
    <a class="btn btn-red" href="#menu">VIEW MORE</a>
    <a class="btn btn-black" href="#reserve">BOOK A TABLE</a>
  </div>
</section>

<section class="section takeout" id="takeout">
  <h2 class="section-title">TAKE <span class="accent">OUT</span></h2>
  <div class="arrow" style="left:70px;top:284px"><svg width="14" height="14" viewBox="0 0 14 14"><path d="M9 2 L4 7 L9 12" fill="none" stroke="#555" stroke-width="2"/></svg></div>
  <div class="takeout-photos">
    <div class="photo" role="img" aria-label="Grilled meat platter" style="background:linear-gradient(135deg,#6a5a4a,#a08a6a 50%,#4a3a2e)"></div>
    <div class="photo" role="img" aria-label="Tacos with fresh toppings" style="background:linear-gradient(135deg,#5a3a4a,#b07a5a 50%,#3a4a2a)"></div>
    <div class="photo" role="img" aria-label="Pasta dish with greens" style="background:linear-gradient(135deg,#d8c8a8,#c89a6a 50%,#8a6a4a)"></div>
    <div class="photo" role="img" aria-label="Fish plate with salad" style="background:linear-gradient(135deg,#3a3a30,#8a5a3a 50%,#4a5a2a)"></div>
  </div>
  <div class="arrow" style="left:1084px;top:284px"><svg width="14" height="14" viewBox="0 0 14 14"><path d="M5 2 L10 7 L5 12" fill="none" stroke="#555" stroke-width="2"/></svg></div>
  <div class="actions">
    <a class="btn btn-red" href="#takeout">VIEW MORE</a>
    <a class="btn btn-black" href="#reserve">BOOK A TABLE</a>
  </div>
</section>

<section class="section reserve" id="reserve">
  <div class="reserve-photo" role="img" aria-label="Outdoor patio with colourful seating and plants"></div>
  <div class="reserve-card">
    <h2>RESERVATIONS</h2>
    <div class="form">
      <div class="field">Enter Name</div>
      <div class="field">Enter Email</div>
      <div class="field">Phone Number</div>
      <div class="field">Date &amp; Time
        <svg width="14" height="14" viewBox="0 0 14 14"><rect x="1" y="2" width="12" height="11" fill="none" stroke="#666"/><path d="M1 5 H13 M4 1 V3 M10 1 V3" stroke="#666"/></svg>
      </div>
      <div class="field full">Message</div>
    </div>
    <div class="submit"><a class="btn btn-red" href="#reserve">SUBMIT</a></div>
  </div>
</section>

<section class="section contact" id="contact">
  <h2 class="section-title">CONTACT <span class="accent">US</span></h2>
  <div class="contact-cols">
    <div>
      <h3>Canada Day Hours!</h3>
      <p>Thursday, July 1st &nbsp;– 5pm<br>Friday, July 2nd &nbsp;– 5pm<br>Saturday, July 3rd &nbsp;– 5pm<br>Sunday, July 4th &nbsp;– Closed</p>
    </div>
    <div>
      <h3>Takeout &amp; Kitchen Hours</h3>
      <p>Thursday to Sunday<br>12:00pm – 9:00pm</p>
      <h3 class="spaced">Outdoor Dining Hours</h3>
      <p>Our patio is open<br>Thursday to Sunday<br>12:00pm – 9:00pm</p>
    </div>
    <div>
      <h3>Get In Touch</h3>
      <ul class="info">
        <li><svg width="12" height="16" viewBox="0 0 12 16"><path d="M6 0 C2.7 0 0 2.6 0 6 C0 10 6 16 6 16 C6 16 12 10 12 6 C12 2.6 9.3 0 6 0 Z" fill="#333"/><circle cx="6" cy="6" r="2.2" fill="#fff"/></svg>12 Ember Lane, Bexwell</li>
        <li><svg width="14" height="14" viewBox="0 0 14 14"><path d="M3 1 L5 1 L6 4 L4.5 5.5 C5.3 7.2 6.8 8.7 8.5 9.5 L10 8 L13 9 L13 11 C13 12 12 13 11 13 C5.5 13 1 8.5 1 3 C1 2 2 1 3 1 Z" fill="#333"/></svg>555-014-2290</li>
        <li><svg width="14" height="12" viewBox="0 0 14 12"><rect x="0.5" y="0.5" width="13" height="11" fill="none" stroke="#333"/><path d="M0.5 0.5 L7 6.5 L13.5 0.5" fill="none" stroke="#333"/></svg>hello@lumbrabexwell.example</li>
      </ul>
    </div>
  </div>
</section>

<footer class="section footer">
  <svg class="wave" style="top:-28px" viewBox="0 0 1200 40"><rect width="1200" height="40" fill="url(#scallop-black)"/></svg>
  Copyright © 2021 Lumbra. All Rights Reserved. | Privacy Policy | Terms and Use
</footer>

</body>
</html>
```